my personal cards just intrducing my self

Massage Therapy to get my name out their

Target Market(s)

40 year olds who enjoy massage

Industry/Entity Type

Massage

Contact Information for Business Card

Marcus T Belwether
LMT-Licensed Massage Therapist
*Swedish *Deep Tissue *Prenatal
*Reflexology *Chair and more

(602)-837-2146
marcusbelwether@velmoranet.com

Font styles to use
Serif

Colors
0456a4
6b449b

```html
<!DOCTYPE html>
<html lang="en">
<head>
<meta charset="utf-8">
<title>Marcus T Belwether – Business Card</title>
<link href="https://fonts.googleapis.com/css2?family=Tinos:ital,wght@0,400;0,700;1,400&display=swap" rel="stylesheet">
<style>
  :root{
    --blue:#0456a4;
    --purple:#6b449b;
    --ink:#1a1a1a;
    --card-white:#ffffff;
    --card-dark:#0c0f14;
    --band-dark:#101318;
    --faint:#e6e6e6;
    --stage:#ecebe8;
  }
  *{box-sizing:border-box;margin:0;padding:0}
  html,body{width:1200px;height:784px;overflow:hidden}
  body{
    background:var(--stage);
    font-family:"Tinos","Times New Roman",serif;
    display:flex;align-items:center;justify-content:center;gap:40px;
  }
  .card{
    position:relative;width:560px;height:320px;overflow:hidden;
    box-shadow:0 6px 20px rgba(0,0,0,.18);
  }
  /* Back side */
  .card--back{
    background:radial-gradient(ellipse at 50% 40%, #1d232c 0%, var(--card-dark) 75%);
    display:flex;flex-direction:column;align-items:center;justify-content:center;
  }
  .brand{display:flex;align-items:center;gap:10px;font-weight:700;color:var(--purple)}
  .brand__dot{width:14px;height:14px;border-radius:50%;background:var(--blue)}
  .card--back .brand{font-size:26px;margin-bottom:26px;color:#8a66c0}
  .back__name{font-size:27px;font-weight:700;color:var(--blue);letter-spacing:.3px}
  .back__rule{width:250px;height:2px;background:var(--purple);margin:4px 0 4px}
  .back__title{font-size:15px;font-style:italic;color:var(--blue);letter-spacing:.6px}

  /* Front side */
  .card--front{background:var(--card-white)}
  .front__brand{position:absolute;left:28px;top:112px;font-size:17px}
  .front__ghost{
    position:absolute;right:-10px;top:70px;font-size:44px;font-weight:700;
    color:var(--faint);transform:rotate(-90deg);transform-origin:right top;
  }
  .front__identity{position:absolute;left:196px;top:62px}
  .front__name{font-size:27px;font-weight:700;color:var(--ink);letter-spacing:.2px}
  .front__rule{width:258px;height:2px;background:var(--purple);margin:4px 0 5px}
  .front__title{font-size:14px;font-style:italic;color:var(--ink);letter-spacing:.8px}
  .contact{position:absolute;left:30px;top:196px;font-size:18px;color:var(--ink);line-height:1.35}
  .contact__row{display:flex;align-items:center;gap:8px}
  .contact__row svg{width:18px;height:18px;flex:none}
  .services{
    position:absolute;left:0;right:0;bottom:0;height:54px;
    background:var(--band-dark);border-top:3px solid var(--purple);
    display:flex;align-items:center;justify-content:space-around;padding:0 12px;
    list-style:none;
  }
  .services li{font-size:15px;color:#8a66c0}
</style>
</head>
<body>
  <section class="card card--back" aria-label="Card back">
    <div class="brand"><span class="brand__dot"></span>Velmora Touch</div>
    <div class="back__name">Marcus T Belwether</div>
    <div class="back__rule"></div>
    <div class="back__title">LMT-Licensed Massage Therapist</div>
  </section>

  <section class="card card--front" aria-label="Card front">
    <div class="front__ghost" aria-hidden="true">Velmora Touch</div>
    <div class="brand front__brand"><span class="brand__dot"></span>Velmora Touch</div>
    <div class="front__identity">
      <div class="front__name">Marcus T Belwether</div>
      <div class="front__rule"></div>
      <div class="front__title">LMT-Licensed Massage Therapist</div>
    </div>
    <div class="contact">
      <div class="contact__row">
        <svg viewBox="0 0 24 24" aria-hidden="true"><path fill="#0456a4" d="M6.6 10.8a15.1 15.1 0 0 0 6.6 6.6l2.2-2.2c.3-.3.7-.4 1-.2 1.1.4 2.3.6 3.6.6.6 0 1 .4 1 1V20c0 .6-.4 1-1 1A17 17 0 0 1 3 4c0-.6.4-1 1-1h3.5c.6 0 1 .4 1 1 0 1.3.2 2.5.6 3.6.1.3 0 .7-.2 1z"/></svg>
        <span>(602)-837-2146</span>
      </div>
      <div class="contact__row">
        <svg viewBox="0 0 24 24" aria-hidden="true"><path fill="#0456a4" d="M12 3 2 12h3v9h5v-6h4v6h5v-9h3z"/></svg>
        <span>marcusbelwether@velmoranet.com</span>
      </div>
    </div>
    <ul class="services">
      <li>Swedish</li><li>Deep Tissue</li><li>Prenatal</li><li>Reflexology</li><li>Chair and more</li>
    </ul>
  </section>
</body>
</html>
```